Kelvaro.ch is looking for business card letterhead and envelope C5 with WOW effect

We need a strong business card for our company Kelvaro.ch, logo is available. You want a black or dark background on which the logo Stark r% 26 # 252; appears. Letterhead and envelope in C5 format should be in a similar design, but does not have to be We need a strong business card for our company Kelvaro.ch, logo is available. A black or dark background is desired, on which the logo Stark comes across. The letterhead and the envelope in C5 format should have a similar design.

Target Market(s)

Private customers as well as entrepreneurs

Contact Information for Business Card

E-mail: info@kelvaro-example.ch
Web.www.Kelvaro-example.ch
Tel: +41 ( 0 ) 79 482 6037
Adresse:
Lindenweg 14
9406 Tarnbach

Hier kann man Icons verwenden für Email,Tel und Adressse

Font styles to use
Other font styles liked:
• Dubai,bold

Colors

Designer to choose colors to be used in the design.

Requirements
Must have
• WOW effect
Nice to have
• R% 26 # 252; back business card with our service listings. - VEHICLE LABELING - SHOP WINDOW LABELING - STICKERS AND MUCH MORE ... in red color

```html
<!DOCTYPE html>
<html lang="en">
<head>
<meta charset="utf-8">
<title>Kelvaro.ch Business Card</title>
<link rel="stylesheet" href="https://fonts.googleapis.com/css2?family=Lato:wght@400;700&display=swap">
<style>
  :root {
    --bg: #e0e0e0;
    --card-dark: #141517;
    --card-light: #333436;
    --accent: #f7c516;
    --text: #f2f2f2;
    --rule: #8a8a8a;
    --mark-grey: #7a7a7a;
    --pattern-tone: #4a4436;
  }
  * { box-sizing: border-box; margin: 0; padding: 0; }
  html, body {
    width: 1200px; height: 960px; overflow: hidden;
    background: var(--bg);
    font-family: "Lato", sans-serif;
  }
  .canvas { position: relative; width: 1200px; height: 960px; }
  .card {
    position: absolute; left: 281px; width: 655px; height: 375px;
    border-radius: 24px; overflow: hidden;
    background: linear-gradient(160deg, var(--card-light) 0%, var(--card-dark) 60%, var(--card-dark) 100%);
    color: var(--text);
  }
  .card--front { top: 80px; }
  .card--back { top: 506px; }

  .brand {
    position: absolute; display: flex; align-items: center; gap: 12px;
    font-weight: 700; letter-spacing: 0.5px;
  }
  .brand__dot { width: 22px; height: 22px; border-radius: 50%; background: var(--accent); }
  .card--front .brand { left: 58px; top: 171px; font-size: 27px; color: var(--text); }

  .divider {
    position: absolute; left: 317px; top: 93px; width: 1px; height: 185px;
    background: var(--rule);
  }
  .contact { position: absolute; left: 338px; top: 92px; }
  .contact__name { font-size: 27px; font-weight: 700; color: var(--accent); line-height: 1.1; }
  .contact__role { font-size: 17.5px; margin-top: 4px; }
  .contact__list { list-style: none; margin-top: 22px; font-size: 17.5px; }
  .contact__item { display: flex; align-items: center; gap: 10px; height: 24px; }
  .contact__item--address { margin-bottom: 15px; }
  .contact__icon { width: 14px; height: 14px; flex: none; }

  .pattern {
    position: absolute; left: 0; top: 0; width: 330px; height: 375px;
    background: linear-gradient(100deg, var(--pattern-tone) 0%, rgba(74,68,54,0.55) 55%, rgba(74,68,54,0) 100%);
    opacity: 0.6;
  }
  .card--back .brand {
    left: 205px; top: 141px; font-size: 34px; color: var(--mark-grey);
  }
  .card--back .brand__dot { width: 28px; height: 28px; border-radius: 0; background: var(--mark-grey); }
  .back-web {
    position: absolute; left: 0; right: 0; top: 292px; text-align: center;
    font-size: 17.5px; color: var(--text);
  }
</style>
</head>
<body>
<main class="canvas">
  <section class="card card--front">
    <div class="brand"><span class="brand__dot"></span><span>Kelvaro.ch</span></div>
    <div class="divider"></div>
    <div class="contact">
      <p class="contact__name">Jonas Berger</p>
      <p class="contact__role">Managing Director</p>
      <ul class="contact__list">
        <li class="contact__item contact__item--address">
          <svg class="contact__icon" viewBox="0 0 14 14"><path d="M7 1a4.3 4.3 0 0 0-4.3 4.3C2.7 8.5 7 13 7 13s4.3-4.5 4.3-7.7A4.3 4.3 0 0 0 7 1zm0 6a1.7 1.7 0 1 1 0-3.4A1.7 1.7 0 0 1 7 7z" fill="var(--accent)"/></svg>
          Lindenweg 14, 9406 Tarnbach
        </li>
        <li class="contact__item">
          <svg class="contact__icon" viewBox="0 0 14 14"><path d="M3 1.5l2.2 2.4-1.2 1.5c.8 1.8 2.2 3.2 4 4l1.5-1.2 2.4 2.2-1.4 2c-4.6-.6-8.5-4.5-9-9z" fill="var(--accent)"/></svg>
          +41 ( 0 ) 79 482 6037
        </li>
        <li class="contact__item">
          <svg class="contact__icon" viewBox="0 0 14 14"><rect x="1" y="3" width="12" height="8" fill="var(--accent)"/><path d="M1 3l6 4.5L13 3" stroke="var(--card-dark)" stroke-width="1.2" fill="none"/></svg>
          info@kelvaro-example.ch
        </li>
        <li class="contact__item">
          <svg class="contact__icon" viewBox="0 0 14 14" fill="none" stroke="var(--accent)" stroke-width="1.1"><circle cx="7" cy="7" r="5.6"/><ellipse cx="7" cy="7" rx="2.5" ry="5.6"/><path d="M1.4 7h11.2M2.3 4.2h9.4M2.3 9.8h9.4"/></svg>
          www.kelvaro-example.ch
        </li>
      </ul>
    </div>
  </section>

  <section class="card card--back">
    <div class="pattern" role="img" aria-label="Faint decorative pattern fading in from the left edge"></div>
    <div class="brand"><span class="brand__dot"></span><span>Kelvaro.ch</span></div>
    <p class="back-web">www.kelvaro-example.ch</p>
  </section>
</main>
</body>
</html>
```